Retail Jewelry Business Card Design Project

We are in need of a new business card design for a retail jewelry store. This store is in the business of fine jewelry including but not specific to bridal jewelry, diamonds, designer jewelry and watches.

This store has been in business for 20 years but continues to strive for a modern professional appeal. The main colors use for this business are a royal blue, white and silver.

Target Market(s)

Target market is ages 18-50

Industry/Entity Type

Jewelry

Requirements
Must have
• Sales Person Name
Sales Person Email Address

Store Address
Store Phone
Website

Standard business card size. No odd shapes or sizes.
Nice to have
• Overall modern feel for card.

We have thought that a design with a nice feature of the logo on the back of the card would be nice but open to ideas.
Should not have
• No specific images of jewelry should be used.

```html
<!DOCTYPE html>
<html lang="en">
<head>
<meta charset="utf-8">
<title>Hollis Reed Fine Jewelry – Business Cards</title>
<link rel="stylesheet" href="https://fonts.googleapis.com/css2?family=PT+Sans:wght@400&display=swap">
<style>
  :root {
    --royal: #2e3192;
    --lavender: #7670b4;
    --white: #ffffff;
    --ink: #333333;
    --label: #2a2a2a;
    --rule: #8a86c4;
    --stage: #ece8e3;
  }
  * { margin: 0; padding: 0; box-sizing: border-box; }
  html, body { width: 1200px; height: 788px; overflow: hidden; }
  body {
    position: relative;
    background: var(--stage);
    font-family: "PT Sans", sans-serif;
  }
  .view-label {
    position: absolute;
    width: 525px;
    text-align: center;
    font-size: 21px;
    color: var(--label);
  }
  .card {
    position: absolute;
    width: 525px;
    height: 300px;
    border-radius: 22px;
    overflow: hidden;
  }
  .card--white { background: var(--white); }
  .card--royal { background: var(--royal); }
  .card--lavender { background: var(--lavender); }

  .brand {
    position: absolute;
    text-align: center;
    font-weight: 400;
    line-height: 1;
  }
  .brand__name { display: block; }
  .brand__line { display: block; letter-spacing: 3px; text-transform: uppercase; }

  .brand--small { left: 0; width: 261px; top: 112px; color: var(--royal); }
  .brand--small .brand__name { font-size: 40px; }
  .brand--small .brand__line { font-size: 15px; margin-top: 8px; }

  .brand--large { left: 0; width: 525px; top: 78px; }
  .brand--large .brand__name { font-size: 66px; }
  .brand--large .brand__line { font-size: 22px; margin-top: 12px; }
  .card--white .brand--large, .card--lavender .brand--large { color: var(--royal); }
  .card--royal .brand--large { color: var(--white); }

  .site-url {
    position: absolute;
    left: 0; width: 525px; top: 259px;
    text-align: center;
    font-size: 14px;
    letter-spacing: 2px;
  }
  .card--white .site-url { color: var(--royal); }
  .card--royal .site-url { color: var(--white); }
  .card--lavender .site-url { color: #1f1f4a; }

  .contact-divider {
    position: absolute;
    left: 261px; top: 40px;
    width: 1px; height: 214px;
    background: var(--rule);
  }
  .contact-rule {
    position: absolute;
    left: 261px; width: 215px; height: 1px;
    background: var(--rule);
  }
  .contact-name {
    position: absolute;
    left: 273px; top: 48px;
    font-size: 17px;
    color: var(--royal);
  }
  .contact-item {
    position: absolute;
    left: 273px;
    display: flex;
    align-items: flex-start;
    gap: 6px;
    font-size: 13.5px;
    line-height: 18px;
    color: var(--ink);
  }
  .contact-item svg { width: 12px; height: 12px; margin-top: 3px; flex: none; fill: var(--ink); }
</style>
</head>
<body>

  <div class="view-label" style="left:55px; top:33px;">Front</div>
  <div class="view-label" style="left:621px; top:33px;">Back - 1</div>
  <div class="view-label" style="left:54px; top:404px;">Back - 2</div>
  <div class="view-label" style="left:622px; top:404px;">Back - 3</div>

  <!-- Front -->
  <section class="card card--white" style="left:55px; top:73px;">
    <div class="brand brand--small">
      <span class="brand__name">Hollis Reed</span>
      <span class="brand__line">Fine Jewelry</span>
    </div>

    <div class="contact-divider"></div>
    <div class="contact-name">Hollis Reed Carlow</div>
    <div class="contact-rule" style="top:84px;"></div>

    <div class="contact-item" style="top:103px;">
      <svg viewBox="0 0 12 12" aria-hidden="true"><path d="M2.5 1 L4.5 1 L5.2 3.6 L3.9 4.6 C4.5 6 5.9 7.4 7.3 8 L8.3 6.8 L11 7.5 L11 9.5 C11 10.4 10.3 11 9.4 11 C4.8 10.6 1.4 7.2 1 2.6 C1 1.7 1.6 1 2.5 1 Z"/></svg>
      <span>555-203-4815</span>
    </div>
    <div class="contact-rule" style="top:141px;"></div>

    <div class="contact-item" style="top:148px;">
      <svg viewBox="0 0 12 12" aria-hidden="true"><path d="M1 3 L6 6.5 L11 3 L11 10 L1 10 Z M1.5 2 L10.5 2 L6 5.2 Z"/></svg>
      <span>hollis@hollisreedjewelry.com</span>
    </div>
    <div class="contact-item" style="top:172px;">
      <svg viewBox="0 0 12 12" aria-hidden="true"><path d="M6 0.8 A5.2 5.2 0 1 0 6 11.2 A5.2 5.2 0 1 0 6 0.8 Z M6 1.8 C6.8 2.6 7.3 4 7.4 5.5 L4.6 5.5 C4.7 4 5.2 2.6 6 1.8 Z M4.6 6.5 L7.4 6.5 C7.3 8 6.8 9.4 6 10.2 C5.2 9.4 4.7 8 4.6 6.5 Z M1.9 5.5 C2.1 3.8 3.2 2.5 4.6 2 C4 3 3.7 4.2 3.6 5.5 Z M8.4 5.5 C8.3 4.2 8 3 7.4 2 C8.8 2.5 9.9 3.8 10.1 5.5 Z M1.9 6.5 L3.6 6.5 C3.7 7.8 4 9 4.6 10 C3.2 9.5 2.1 8.2 1.9 6.5 Z M8.4 6.5 L10.1 6.5 C9.9 8.2 8.8 9.5 7.4 10 C8 9 8.3 7.8 8.4 6.5 Z"/></svg>
      <span>www.hollisreedjewelry.com</span>
    </div>
    <div class="contact-rule" style="top:198px;"></div>

    <div class="contact-item" style="top:209px;">
      <svg viewBox="0 0 12 12" aria-hidden="true"><path d="M6 1 L11.5 6 L10 6 L10 11 L7.3 11 L7.3 8 L4.7 8 L4.7 11 L2 11 L2 6 L0.5 6 Z"/></svg>
      <span>2230 Lindell Street<br>Bayport, FL 32599</span>
    </div>
  </section>

  <!-- Back 1 -->
  <section class="card card--white" style="left:621px; top:73px;">
    <div class="brand brand--large">
      <span class="brand__name">Hollis Reed</span>
      <span class="brand__line">Fine Jewelry</span>
    </div>
    <div class="site-url">www.hollisreedjewelry.com</div>
  </section>

  <!-- Back 2 -->
  <section class="card card--royal" style="left:54px; top:445px;">
    <div class="brand brand--large">
      <span class="brand__name">Hollis Reed</span>
      <span class="brand__line">Fine Jewelry</span>
    </div>
    <div class="site-url">www.hollisreedjewelry.com</div>
  </section>

  <!-- Back 3 -->
  <section class="card card--lavender" style="left:622px; top:445px;">
    <div class="brand brand--large">
      <span class="brand__name">Hollis Reed</span>
      <span class="brand__line">Fine Jewelry</span>
    </div>
    <div class="site-url">www.hollisreedjewelry.com</div>
  </section>

</body>
</html>
```